Dental Medical History Form - Content provided

Design a medical history form for a dental practice. Content is provided so all that is needed is the formatting to make it look great and easy to read.

"Patient Information" to include all information contained in top portion of the "Patient Medical History Form" docx file.

"Medical History" should follow the formatting and content of the "Exact Medical History" file as this is what the entry fields look like in our practice software and so we would like it to match.

1st page - Patient info, allergies, medications, antibiotics, joint replacement, pregnancy.

2nd page - Do you have, or have you had, any of the following? . . . . . . .
Updates

Target Market(s)

All ages but must be clear enough for elderly to read. Use as much space as possible to keep font size bigger yet keep to two pages

Industry/Entity Type

Dental

Font styles to use
Sans Serif

Requirements
Must have
• All content provided
• Our logo at the top (file provided)
• Century Gothic Font
• Limit to two pages

```html
<!DOCTYPE html>
<html lang="en">
<head>
<meta charset="utf-8">
<title>Harbour Dental – Confidential Medical History</title>
<link href="https://fonts.googleapis.com/css2?family=Questrial&display=swap" rel="stylesheet">
<style>
:root{
  --ink:#36434d;
  --band:#3b4852;
  --line:#8c959c;
  --paper:#f7f7f7;
  --bg:#ffffff;
  --white:#ffffff;
}
*{box-sizing:border-box;margin:0;padding:0}
html,body{width:1200px;height:816px;overflow:hidden;background:var(--bg)}
body{font-family:"Questrial",sans-serif;color:var(--ink);position:relative}
.page{position:absolute;top:8px;height:800px;background:var(--paper);box-shadow:0 0 4px rgba(0,0,0,.18)}
.page--front{left:26px;width:557px}
.page--back{left:608px;width:566px}
.brand{position:absolute;left:20px;top:30px;font-size:30px;line-height:1;letter-spacing:.5px;color:var(--ink);display:flex;align-items:center;gap:8px}
.brand__dot{width:9px;height:9px;border:1.5px solid var(--line)}
.practice-address{position:absolute;right:22px;top:29px;text-align:right;font-size:10px;line-height:12px}
.form-title{position:absolute;left:0;right:0;top:100px;text-align:center;font-size:16px;letter-spacing:1.8px;font-weight:700}
.band{position:absolute;left:0;right:0;height:15px;background:var(--band);color:var(--white);font-size:9px;text-align:center;line-height:15px;letter-spacing:.3px}
.row{position:absolute;left:25px;right:26px;height:14px;display:flex;align-items:center;gap:4px;font-size:9.5px;white-space:nowrap}
.field{height:11px;border:1px solid var(--line);background:var(--white);flex:1}
.digit{width:12px;height:11px;border:1px solid var(--line);background:var(--white);flex:none}
.gap{width:5px;flex:none}
.box{width:11px;height:11px;border:1px solid var(--line);background:var(--white);flex:none;display:inline-block}
.opt{display:flex;align-items:center;gap:6px}
.spread{justify-content:space-between}
.col-heads{position:absolute;top:155px;left:0;right:0;font-size:9px}
.col-heads span{position:absolute;transform:translateX(-50%)}
.rule{position:absolute;height:1px;background:var(--line)}
.qa{position:absolute;left:25px;height:14px;display:flex;align-items:center;font-size:9.5px}
.qa .q{width:170px}
.qa .opt{margin-right:22px}
.tab{position:absolute;bottom:0;height:15px;background:var(--band);color:var(--white);font-size:11px;text-align:center;line-height:16px;border-radius:8px 8px 0 0}
.title-band{position:absolute;left:0;right:0;top:0;height:22px;background:var(--band);color:var(--white);font-size:14px;text-align:center;line-height:22px}
.list{position:absolute;top:32px;display:flex;flex-direction:column}
.item{height:18.13px;display:flex;align-items:center;font-size:9.5px;white-space:nowrap}
.item .box{margin-right:21px}
.tag{height:18.13px;display:flex;align-items:center;padding-left:32px}
.tag span{background:var(--band);color:var(--white);font-size:9px;line-height:11px;padding:0 4px;width:66px}
.tag span.wide{width:90px}
.note{font-size:8.5px;height:18.13px;display:flex;align-items:center;margin-left:-10px}
.entry{width:222px;height:14px;border:1px solid var(--line);background:var(--white);margin:4px 0 6.2px -10px}
.sign{position:absolute;top:725px;left:35px;right:30px;display:flex;align-items:flex-end;font-size:11.5px;gap:4px}
.sign .blank{border-bottom:1px solid var(--line);height:1px;margin-bottom:3px}
.thanks{position:absolute;left:0;right:0;top:752px;text-align:center;font-size:8.5px;line-height:13.5px}
</style>
</head>
<body>

<section class="page page--front">
  <div class="brand"><span>Harbour Dental</span><span class="brand__dot"></span></div>
  <address class="practice-address" style="font-style:normal">3.04/150 Seaview Road<br>Kincumber NSW 2251<br>(02) 4300 1234</address>
  <h1 class="form-title">CONFIDENTIAL MEDICAL HISTORY</h1>

  <div class="band" style="top:133px">General Information</div>
  <div class="col-heads"><span style="left:81px">Title</span><span style="left:176px">First</span><span style="left:320px">Last</span><span style="left:463px">Preferred</span></div>
  <div class="row" style="top:169px">Name:<span class="field" style="flex:0 0 43px"></span><span class="gap"></span><span class="field"></span><span class="gap"></span><span class="field"></span><span class="gap"></span><span class="field"></span></div>
  <div class="row" style="top:195px">Address:<span class="field"></span></div>
  <div class="row" style="top:221px">Email Address:<span class="field" style="flex:0 0 278px"></span>&nbsp;DOB:<span class="digit"></span><span class="digit"></span><span class="gap"></span><span class="digit"></span><span class="digit"></span><span class="gap"></span><span class="digit"></span><span class="digit"></span><span class="digit"></span><span class="digit"></span></div>
  <div class="row" style="top:247px">Mobile<span class="field"></span>&nbsp;Work<span class="field"></span>&nbsp;Home<span class="field"></span></div>
  <div class="row" style="top:273px">Emergency Contact Person:<span class="field"></span></div>
  <div class="row" style="top:299px">Emergency Contact Relationship:<span class="field" style="flex:0 0 151px"></span>&nbsp;&nbsp;Phone:<span class="field"></span></div>
  <div class="row" style="top:326px">General Practitioner Name:<span class="field" style="flex:0 0 204px"></span>&nbsp;&nbsp;Phone:<span class="field"></span></div>
  <div class="row" style="top:351px">General Practitioner Address:<span class="field"></span></div>
  <div class="row" style="top:378px">Do you have dental health fund cover?<span class="box"></span>Yes<span class="box"></span>&nbsp;No&nbsp;&nbsp;If so, Name of Fund:<span class="field"></span></div>
  <div class="row" style="top:404px">Fund Number:<span class="field" style="flex:0 0 189px"></span>&nbsp;&nbsp;Priority Number on card:1<span class="box"></span>2<span class="box"></span>3<span class="box"></span>4<span class="box"></span>5<span class="box"></span>6<span class="box"></span></div>
  <div class="row" style="top:430px">Occupation:<span class="field" style="flex:0 0 189px"></span>&nbsp;&nbsp;Referred by:<span class="field"></span></div>

  <div class="band" style="top:456px">Please indicate if you are allergic to any of the following ?</div>
  <div class="row spread" style="top:487px">
    <span class="opt"><span class="box"></span>Codeine</span><span class="opt"><span class="box"></span>Penicillin</span><span class="opt"><span class="box"></span>Sulphites</span><span class="opt"><span class="box"></span>Latex</span><span class="opt"><span class="box"></span>Local Anaesthetic</span><span class="opt"><span class="box"></span>Lactose</span><span class="opt"><span class="box"></span>Metal</span>
  </div>
  <div class="row" style="top:513px">Other:<span class="field"></span></div>

  <div class="band" style="top:541px">Are you currently taking, or have ever taken, any of the following medication ?</div>
  <div class="row" style="top:568px;gap:14px">
    <span class="opt"><span class="box"></span>Asthma inhaler</span><span class="opt"><span class="box"></span>Anti-epileptics</span><span class="opt"><span class="box"></span>Anti-depressants</span><span class="opt"><span class="box"></span>Blood Pressure</span><span class="opt"><span class="box"></span>Blood Thinners</span>
  </div>
  <div class="row spread" style="top:594px">
    <span class="opt"><span class="box"></span>Bisphosphonates</span><span class="opt"><span class="box"></span>Chemotherapy</span><span class="opt"><span class="box"></span>Insulin</span><span class="opt"><span class="box"></span>Immunosuppressants</span><span class="opt"><span class="box"></span>Steroids</span><span class="opt"><span class="box"></span>&nbsp;&nbsp;&nbsp;&nbsp;Other</span>
  </div>

  <div class="band" style="top:624px">Please specify medication name, dose, and frequency where possible:</div>
  <div class="rule" style="top:656px;left:25px;width:164px"></div><div class="rule" style="top:656px;left:196px;width:164px"></div><div class="rule" style="top:656px;left:366px;width:165px"></div>
  <div class="rule" style="top:677px;left:25px;width:164px"></div><div class="rule" style="top:677px;left:196px;width:164px"></div><div class="rule" style="top:677px;left:366px;width:165px"></div>
  <div class="rule" style="top:698px;left:25px;width:164px"></div><div class="rule" style="top:698px;left:196px;width:164px"></div><div class="rule" style="top:698px;left:366px;width:165px"></div>

  <div class="qa" style="top:712px"><span class="q">Do you require antibiotic cover?</span><span class="opt"><span class="box"></span>&nbsp;&nbsp;Yes</span><span class="opt"><span class="box"></span>&nbsp;&nbsp;&nbsp;No</span></div>
  <div class="qa" style="top:735px"><span class="q">Have you had a joint replacement?</span><span class="opt"><span class="box"></span>&nbsp;&nbsp;Yes</span><span class="opt"><span class="box"></span>&nbsp;&nbsp;&nbsp;No</span></div>
  <div class="qa" style="top:759px"><span class="q">Women:&nbsp; Are you pregnant?</span><span class="opt"><span class="box"></span>&nbsp;&nbsp;Yes</span><span class="opt"><span class="box"></span>&nbsp;&nbsp;&nbsp;No</span><span class="opt"><span class="box"></span>Possible</span><span class="opt" style="gap:4px"><span class="box"></span><span class="box"></span>&nbsp;&nbsp;&nbsp;How Many Weeks?</span></div>

  <div class="tab" style="left:212px;width:132px">Please Turn Over</div>
</section>

<section class="page page--back">
  <div class="title-band">Do you have, or have you had, any of the following?</div>

  <div class="list" style="left:35px">
    <div class="tag"><span>Dental</span></div>
    <div class="item"><span class="box"></span>Acid Reflux</div>
    <div class="item"><span class="box"></span>Bad Breath/Taste</div>
    <div class="item"><span class="box"></span>Bleeding/Swollen/Sore Gums</div>
    <div class="item"><span class="box"></span>Blisters/Ulcers in Mouth</div>
    <div class="item"><span class="box"></span>Broken tooth/filling</div>
    <div class="item"><span class="box"></span>Burning tongue</div>
    <div class="item"><span class="box"></span>Dry mouth</div>
    <div class="item"><span class="box"></span>Food collection between teeth</div>
    <div class="item"><span class="box"></span>Grinding/clenching teeth (day/night)</div>
    <div class="item"><span class="box"></span>Loose teeth</div>
    <div class="item"><span class="box"></span>Crooked teeth</div>
    <div class="item"><span class="box"></span>Discoloured teeth</div>
    <div class="item"><span class="box"></span>Sensitivity to Hot/Cold</div>
    <div class="item"><span class="box"></span>Tooth pain when chewing</div>
    <div class="item"><span class="box"></span>Jaw pain/Fracture</div>
    <div class="item"><span class="box"></span>Orthodontic treatment/history</div>
    <div class="item"><span class="box"></span>Oral Cancer</div>
    <div class="tag"><span>Diet/Lifestyle</span></div>
    <div class="item"><span class="box"></span>Drink more than one glass alcohol per day</div>
    <div class="item"><span class="box"></span>Smoking</div>
    <div class="item"><span class="box"></span>Carbonated drinks</div>
    <div class="item"><span class="box"></span>Sugary foods</div>
    <div class="tag"><span>Blood</span></div>
    <div class="item"><span class="box"></span>Anaemia</div>
    <div class="item"><span class="box"></span>Blood clots</div>
    <div class="item"><span class="box"></span>Leukemia</div>
    <div class="item"><span class="box"></span>Low platelets</div>
    <div class="tag"><span>Chest</span></div>
    <div class="item"><span class="box"></span>Bronchitis</div>
    <div class="item"><span class="box"></span>Emphysema</div>
    <div class="item"><span class="box"></span>Pneumonia</div>
    <div class="tag"><span class="wide">Infectious Disease</span></div>
    <div class="item"><span class="box"></span>Hepatitis A,B,C,D</div>
    <div class="item"><span class="box"></span>HIV/AIDS</div>
    <div class="item"><span class="box"></span>Tuberculosis</div>
  </div>

  <div class="list" style="left:331px">
    <div class="tag"><span style="width:48px">Heart</span></div>
    <div class="item"><span class="box"></span>Angina</div>
    <div class="item"><span class="box"></span>Atrial Fibrillation</div>
    <div class="item"><span class="box"></span>Congenital Heart Disease</div>
    <div class="item"><span class="box"></span>Heart attack</div>
    <div class="item"><span class="box"></span>Heart murmur</div>
    <div class="item"><span class="box"></span>Heart surgery</div>
    <div class="item"><span class="box"></span>Heart valve replacement</div>
    <div class="item"><span class="box"></span>Infective endocarditis</div>
    <div class="item"><span class="box"></span>Rheumatic Heart Disease</div>
    <div class="item"><span class="box"></span>Pacemaker</div>
    <div class="item"><span class="box"></span>Stent</div>
    <div class="tag"><span style="width:48px">Other</span></div>
    <div class="item"><span class="box"></span>Anxiety/PTSD</div>
    <div class="item"><span class="box"></span>Arthritis</div>
    <div class="item"><span class="box"></span>Alzheimer's</div>
    <div class="item"><span class="box"></span>Asthma</div>
    <div class="item"><span class="box"></span>Anaphylaxis</div>
    <div class="item"><span class="box"></span>Auto-immune disease</div>
    <div class="item"><span class="box"></span>Blood Pressure (High/Low)</div>
    <div class="item"><span class="box"></span>Depression</div>
    <div class="item"><span class="box"></span>Diabetes</div>
    <div class="item"><span class="box"></span>Epilepsy</div>
    <div class="item"><span class="box"></span>Kidney Disease</div>
    <div class="item"><span class="box"></span>Liver Disease</div>
    <div class="item"><span class="box"></span>Osteoporosis</div>
    <div class="item"><span class="box"></span>Radiation to Head/Neck</div>
    <div class="item"><span class="box"></span>Sleep apnea</div>
    <div class="item"><span class="box"></span>Stroke</div>
    <div class="note">Please list any other conditions we should be aware of:</div>
    <div class="entry"></div><div class="entry"></div><div class="entry"></div><div class="entry"></div><div class="entry"></div>
  </div>

  <div class="sign"><span>Signature:</span><span class="blank" style="width:206px"></span><span style="margin-left:18px">Date:</span><span class="blank" style="flex:1"></span></div>
  <p class="thanks">Thank you for the time to complete your medical history form.<br>Oral health is linked to overall health and this comprehensive questionnaire will help us to provide you with optimal and safe care.</p>
  <div class="tab" style="left:216px;width:134px;height:8px"></div>
</section>

</body>
</html>
```